Heron Haulage needs Bussiness cards!

Our new trucking company needs business cards!
We need the same design with two different names and emails, everything else it's the same.
I have included our original logo so we can use it for the design.
Note: the logo to be used is the o e with the buffalo on the right side, next to the letters H and H.

Target Market(s)

Trucking, refrigerated transportation, freight

Industry/Entity Type

Business

Contact Information for Business Card

Card #1:
Marcus Whitfield
marcuswhitfield@heronhaulage.example
1-855-317-6094
(956)238-7160
4117 W. Larkin Ave.
Pharr, TX 78590
www.heronhaulage.example

Card#2:
Rosalba Quintero
rosalba@heronhaulage.example
1-855-317-6094
(956)238-7160
4117 W. Larkin Ave.
Pharr, TX 78590
www.heronhaulage.example

Font styles to use
Sans Serif

Colors
0655a3
ec1f27
ffffff

Requirements
Must have
• our logo
Nice to have
• roads on background,

```html
<!DOCTYPE html>
<html lang="en">
<head>
<meta charset="utf-8">
<title>Heron Haulage – Business Card</title>
<link href="https://fonts.googleapis.com/css2?family=Open+Sans:wght@400;600;800&display=swap" rel="stylesheet">
<style>
  :root {
    --brand-blue: #0655a3;
    --brand-red: #ec1f27;
    --brand-white: #ffffff;
    --card-black: #0d0d0d;
    --backdrop: #3a3431;
    --text-soft: #e6e6e6;
  }
  * { box-sizing: border-box; margin: 0; padding: 0; }
  html, body {
    width: 1200px; height: 900px; overflow: hidden;
    background: var(--backdrop);
    font-family: "Open Sans", Arial, sans-serif;
  }
  .stage {
    position: relative; width: 1200px; height: 900px;
    display: flex; align-items: center; justify-content: center; gap: 60px;
  }
  .card {
    position: relative; width: 520px; height: 298px;
    background: var(--card-black);
    box-shadow: 0 10px 30px rgba(0,0,0,.45);
    overflow: hidden;
  }
  .wordmark {
    display: flex; align-items: center; gap: 10px;
    font-weight: 800; text-transform: uppercase; letter-spacing: .5px; line-height: 1;
    white-space: nowrap;
  }
  .wordmark__dot { width: 14px; height: 14px; border-radius: 50%; flex: none; }
  .card--front .wordmark {
    position: absolute; left: 130px; top: 80px;
    font-size: 32px; color: var(--brand-red);
  }
  .card--front .wordmark__dot { background: var(--brand-blue); }
  .identity {
    position: absolute; left: 20px; top: 172px; width: 170px; text-align: right;
  }
  .identity__name { color: var(--brand-red); font-size: 16px; font-weight: 600; margin-bottom: 16px; white-space: nowrap; }
  .identity__address { color: var(--text-soft); font-size: 13.5px; line-height: 1.45; white-space: nowrap; }
  .divider {
    position: absolute; left: 206px; top: 150px; width: 1px; height: 110px;
    background: linear-gradient(to bottom, transparent, var(--brand-red) 30%, var(--brand-red) 70%, transparent);
  }
  .contacts { position: absolute; left: 220px; top: 152px; list-style: none; }
  .contacts li {
    display: flex; align-items: center; gap: 9px; white-space: nowrap;
    color: var(--text-soft); font-size: 13px; line-height: 1; margin-bottom: 9px;
  }
  .contacts svg { width: 11px; height: 11px; flex: none; fill: var(--brand-red); }
  .card--back { display: flex; align-items: center; justify-content: center; }
  .card--back .wordmark { font-size: 38px; color: var(--brand-white); }
  .card--back .wordmark__dot { background: var(--brand-red); width: 16px; height: 16px; }
</style>
</head>
<body>
<main class="stage">
  <section class="card card--front" aria-label="Business card front">
    <div class="wordmark"><span>Heron Haulage</span><span class="wordmark__dot"></span></div>
    <div class="identity">
      <p class="identity__name">Marcus Whitfield</p>
      <p class="identity__address">4117 W. Larkin Ave.<br>Pharr, TX 78590</p>
    </div>
    <div class="divider"></div>
    <ul class="contacts">
      <li><svg viewBox="0 0 12 12"><rect x="3" y="0" width="6" height="12" rx="1.2"/><rect x="4" y="1.5" width="4" height="7.5" fill="#0d0d0d"/></svg>(956)238-7160</li>
      <li><svg viewBox="0 0 12 12"><path d="M2 0l2.5 0 1 3-1.5 1.2a7 7 0 0 0 3.8 3.8L9 6.5l3 1V10c0 1-1 2-2 2A10 10 0 0 1 0 2c0-1 1-2 2-2z"/></svg>1-855-317-6094</li>
      <li><svg viewBox="0 0 12 12"><rect x="0" y="2" width="12" height="8" rx="1"/><path d="M0.5 2.5L6 7l5.5-4.5" stroke="#0d0d0d" stroke-width="1.2" fill="none"/></svg>marcuswhitfield@heronhaulage.example</li>
      <li><svg viewBox="0 0 12 12"><circle cx="6" cy="6" r="6"/><path d="M0 6h12M6 0c-3 3-3 9 0 12M6 0c3 3 3 9 0 12" stroke="#0d0d0d" stroke-width=".9" fill="none"/></svg>www.heronhaulage.example</li>
    </ul>
  </section>
  <section class="card card--back" aria-label="Business card back">
    <div class="wordmark"><span>Heron Haulage</span><span class="wordmark__dot"></span></div>
  </section>
</main>
</body>
</html>
```